Distribution/Printing company needs a web site to inform prospective customers on what we do.

Distribution/Printing/Packaging company needs a web site to inform prospective customers on what we do. Please look at our direct to consumer web site (under development) for an idea of the product lines we sell: storedev.maplewickhaven.com
Logo files are attached as is a flyer that is under development which contains other information about the company (this is to be used for content- not to be posted as is). The web site should be focused on our business customer base and is not intended to be direct to consumer. Site should have a link to our consumer web site.
Site design should be mobile friendly, or mobile could be redirected to a mobile version. This web site will be strictly informational and will not be designed for any sales transactions.

Target Market(s)

Manufacturing and retail businesses, any other multi-site business that would benefit from centralized pricing and budget controls we can provide (banks, medical/dental offices, educational facilities, etc).

Industry/Entity Type

It Company

Coding

Coded - Design and coding required

Number of Pages Required

5+ page

Requirements
Must have
• 1) Top level menu: Products, about us, locations, contact us, news
• 2) page with news/promotions that is easily updated
• 3) "contact us" form (name, company, phone, email address) email link
• 4) link to www.store.maplewickhaven.com with information that lower pricing is available for businesses
• 5) SEO keywords
• 6) Link to powerpoint presentation file
Nice to have
• 1) our phone number should appear on every page near the top

```html
<!DOCTYPE html>
<html lang="en">
<head>
<meta charset="utf-8">
<title>Maplewick Haven Supply – Packaging, Printing, Distribution</title>
<link href="https://fonts.googleapis.com/css2?family=Montserrat:wght@400;500;600&family=Open+Sans:wght@400;600&display=swap" rel="stylesheet">
<style>
:root{
  --blue:#0b77c8;
  --ink:#222222;
  --text:#555555;
  --muted:#777777;
  --band:#eceef1;
  --tile:#eeeeee;
  --footer:#231f20;
  --footer-bottom:#171415;
  --footer-line:#3a3637;
  --white:#ffffff;
}
*{box-sizing:border-box;margin:0;padding:0}
html,body{width:1200px;height:2161px;overflow:hidden}
body{font-family:"Open Sans",Arial,sans-serif;color:var(--text);background:var(--white);font-size:12px}
.wrap{width:976px;margin:0 auto;position:relative}
h1,h2,h3,h4{font-family:"Montserrat",Arial,sans-serif;font-weight:500;color:var(--ink)}

/* header */
.site-header{height:135px}
.site-header .wrap{height:135px}
.brand{position:absolute;left:0;top:22px;width:240px}
.brand-mark{display:block;width:14px;height:14px;background:var(--ink);margin-bottom:22px}
.brand-name{font-weight:600;font-size:16px;color:var(--ink);line-height:20px;white-space:nowrap}
.brand-tag{font-size:11px;color:var(--ink);font-weight:600;margin-top:2px;white-space:nowrap}
.topbar{position:absolute;right:0;top:0;width:202px;height:46px;background:var(--blue);color:var(--white);font-family:"Montserrat",sans-serif;font-size:11px;display:flex;align-items:center;justify-content:center;gap:12px;white-space:nowrap}
.account{position:absolute;right:172px;top:84px;font-size:11px;color:var(--ink);display:flex;gap:14px;white-space:nowrap}
.account b{color:var(--blue);font-weight:400;margin-right:3px}
.phone-box{position:absolute;right:0;top:68px;width:155px;height:44px;background:var(--ink);color:var(--white);font-size:11px;display:flex;align-items:center;justify-content:center;gap:7px;white-space:nowrap}
.phone-box svg{width:12px;height:12px;fill:var(--white)}

/* nav */
.main-nav{height:61px;background:linear-gradient(#0d80d2,#0a6fbc)}
.main-nav ul{list-style:none;display:flex;justify-content:space-between;height:61px}
.main-nav li{color:var(--white);font-size:12px;display:flex;align-items:center;padding:0 16px;white-space:nowrap}
.main-nav li.active{background:var(--ink);padding:0 32px}

/* hero */
.hero{height:533px;position:relative;background:linear-gradient(#ffffff 0%,#f3f3f3 62%,#e6d3bd 72%,#d7bd9e 100%)}
.hero-photo{position:absolute;left:530px;top:100px;width:670px;height:430px;background:radial-gradient(ellipse at 50% 55%,#9bb0c8 0%,#c9a77e 45%,rgba(215,190,160,0) 75%)}
.hero-copy{position:absolute;left:112px;top:155px;width:390px}
.hero-copy h1{font-size:32px;font-weight:500;letter-spacing:.3px;margin-bottom:12px;white-space:nowrap}
.hero-copy p{font-size:12px;line-height:26px}
.btn{display:inline-block;background:var(--blue);color:var(--white);font-family:"Montserrat",sans-serif;font-size:12px;font-weight:500;height:43px;line-height:43px;padding:0 19px;border-radius:2px;margin-top:20px}
.dots{position:absolute;left:570px;top:500px;display:flex;gap:7px}
.dots i{width:8px;height:8px;border-radius:50%;background:var(--ink);display:block}
.dots i.on{background:var(--blue)}

/* services */
.services{height:324px;background:var(--band);padding-top:33px}
.services .wrap{display:flex;justify-content:space-between}
.service{width:307px;text-align:center}
.service .photo{height:165px;border:4px solid var(--white);box-shadow:0 4px 8px rgba(0,0,0,.15)}
.service h3{font-size:16px;margin:18px 0 6px;letter-spacing:.5px}
.service p{font-size:11.5px;line-height:20px;color:var(--muted)}

/* products */
.shop{height:576px;padding-top:40px}
.shop .wrap{display:flex;gap:25px}
.categories{width:225px}
.section-title{font-size:20px;font-weight:500;letter-spacing:.4px;height:37px;line-height:26px;white-space:nowrap}
.cat{height:70px;background:var(--tile);margin-bottom:7px;display:flex;align-items:center;padding:0 18px;font-family:"Montserrat",sans-serif;font-size:15px;color:var(--ink)}
.cat svg{width:30px;height:30px;margin-right:12px;fill:var(--blue)}
.cat .arrow{margin-left:auto;color:var(--muted);font-size:14px}
.cat.active{background:var(--blue);color:var(--white)}
.cat.active svg{fill:var(--white)}
.cat.active .arrow{color:var(--white)}
.products{width:726px}
.products-head{display:flex;justify-content:space-between}
.view-all{font-family:"Montserrat",sans-serif;color:var(--blue);font-size:12px;margin-top:8px}
.grid{display:grid;grid-template-columns:repeat(3,226px);column-gap:24px;row-gap:24px}
.product .thumb{height:144px;background:#f4f4f4;border:3px solid var(--white);outline:1px solid #e2e2e2;box-shadow:0 5px 8px rgba(0,0,0,.12);display:flex;align-items:center;justify-content:center}
.product .thumb div{width:120px;height:90px;border-radius:6px}
.product .name{text-align:center;font-size:11.5px;margin:18px 0 9px;line-height:16px}
.product .row{display:flex;justify-content:space-between;font-family:"Montserrat",sans-serif;font-size:13px;color:var(--ink);line-height:17px}
.details{color:var(--blue)}

/* features */
.features{height:250px}
.features .wrap{display:flex;justify-content:space-between}
.feature{width:225px;height:216px;border:1px solid #ddd;box-shadow:inset 0 0 14px rgba(0,0,0,.12);text-align:center;padding-top:25px}
.feature .icon{width:71px;height:71px;border-radius:50%;background:#111;margin:0 auto 17px;display:flex;align-items:center;justify-content:center}
.feature .icon svg{width:28px;height:28px;fill:var(--white)}
.feature h4{font-size:12px;font-weight:500;margin-bottom:8px;white-space:nowrap}
.feature p{font-size:11.5px;line-height:21px;color:var(--muted);padding:0 14px}

/* footer */
.site-footer{height:213px;background:var(--footer);color:#c9c9c9}
.site-footer .wrap{display:flex;height:213px;padding-top:34px}
.foot-col{padding:0 30px;border-left:1px solid var(--footer-line)}
.foot-col:first-child{padding-left:0;border:none;width:242px}
.foot-col h4{color:var(--white);font-size:16px;font-weight:500;margin-bottom:14px}
.foot-brand-mark{display:block;width:12px;height:12px;background:#9a9a9a;margin:6px 0 8px}
.foot-brand{color:#d0d0d0;font-weight:600;font-size:13px;white-space:nowrap}
.foot-tag{font-size:9px;margin-bottom:18px}
.foot-about{font-size:11px;line-height:24px}
.contact{width:280px}
.contact li{list-style:none;display:flex;gap:10px;font-size:11.5px;line-height:19px;margin-bottom:8px}
.contact svg{width:13px;height:14px;fill:var(--blue);flex:none;margin-top:3px}
.links{width:282px}
.links ul{list-style:none;display:grid;grid-template-columns:113px 100px;row-gap:8px;font-size:10.5px}
.social{border:none;padding-right:0;margin-left:auto;width:140px}
.social li{list-style:none;font-size:11px;line-height:26px;display:flex;align-items:center;gap:6px}
.social i{width:12px;height:12px;display:block}
.foot-bottom{height:69px;background:var(--footer-bottom)}
.foot-bottom .wrap{display:flex;align-items:center;justify-content:space-between;height:69px;font-size:11px;color:#aaa}
.cards{display:flex;gap:7px}
.cards span{width:35px;height:23px;border-radius:2px;display:block}
</style>
</head>
<body>

<header class="site-header">
  <div class="wrap">
    <div class="brand">
      <span class="brand-mark"></span>
      <div class="brand-name">MAPLEWICK HAVEN SUPPLY</div>
      <div class="brand-tag">Packaging • Printing • Distribution</div>
    </div>
    <div class="topbar"><span>LIVE CHAT</span><span>|</span><span>FAQs</span></div>
    <div class="account"><span><b>●</b>BUSINESS PRICING</span><span><b>●</b>CONSUMER STORE</span></div>
    <div class="phone-box"><svg viewBox="0 0 13 14"><path d="M2 1h3l1 3-2 1.5a8 8 0 004 4L9.5 8l3 1v3a1 1 0 01-1 1A11 11 0 011 2a1 1 0 011-1z"/></svg><span>123 456 789 000</span></div>
  </div>
</header>

<nav class="main-nav">
  <div class="wrap">
    <ul>
      <li class="active">HOME</li><li>PACKAGING</li><li>DISTRIBUTION</li><li>PRINTING</li><li>OUR PRODUCTS</li><li>ABOUT US</li><li>LOCATIONS</li><li>NEWS</li><li>CONTACT US</li>
    </ul>
  </div>
</nav>

<section class="hero">
  <div class="hero-photo" role="img" aria-label="Couple sitting on a wooden floor among cardboard moving boxes"></div>
  <div class="hero-copy">
    <h1>PACKAGING SERVICES</h1>
    <p>Ut wisi enim ad minim veniam, quis nostrud exerci tation ullamcorper suscipit lobortis nisl ut aliquip ex ea commodo consequat. Duis autem vel eum iriure dolor in hendrerit in vulputate.</p>
    <span class="btn">READ MORE ›</span>
  </div>
  <div class="dots"><i></i><i class="on"></i><i></i><i></i></div>
</section>

<section class="services">
  <div class="wrap">
    <div class="service">
      <div class="photo" role="img" aria-label="Team working around a laptop with parcels" style="background:linear-gradient(135deg,#8a97a8,#c9ccd2 55%,#b89a78)"></div>
      <h3>DISTRIBUTION</h3>
      <p>Lorem ipsum dolor sit amet, consectetuer adipiscing elit, sed diam nonummy nibh euismod tincidunt.</p>
    </div>
    <div class="service">
      <div class="photo" role="img" aria-label="Warehouse worker checking boxes on a tablet" style="background:linear-gradient(135deg,#b89470,#d8c3a6 50%,#9aa3ad)"></div>
      <h3>PACKAGING</h3>
      <p>Ut wisi enim ad minim veniam, quis nostrud exerci tation ullamcorper suscipit lobortis nisl.</p>
    </div>
    <div class="service">
      <div class="photo" role="img" aria-label="Printing press rollers in cyan, magenta and yellow ink" style="background:linear-gradient(160deg,#7b7b7b 0%,#f0d21d 30%,#e0209a 55%,#1aa3e0 80%,#555 100%)"></div>
      <h3>PRINTING</h3>
      <p>Eodem modo typi, qui nunc nobis videntur parum clari, fiant sollemnes in futurum.</p>
    </div>
  </div>
</section>

<section class="shop">
  <div class="wrap">
    <aside class="categories">
      <h2 class="section-title">CATEGORIES</h2>
      <div class="cat"><svg viewBox="0 0 32 32"><path d="M4 10l12-6 12 6v13l-12 6-12-6z"/></svg>PACKAGING<span class="arrow">›</span></div>
      <div class="cat"><svg viewBox="0 0 32 32"><path d="M20 3l9 9-5 1-6 6 1 6-3 2-5-6-7 8-1-1 8-7-6-5 2-3 6 1 6-6z"/></svg>OFFICE<span class="arrow">›</span></div>
      <div class="cat"><svg viewBox="0 0 32 32"><path d="M3 11l13-6 13 6-13 6zM4 13l11 6v10L4 23zM28 13v10l-11 6V19z"/></svg>STORAGE<span class="arrow">›</span></div>
      <div class="cat"><svg viewBox="0 0 32 32"><path d="M11 3h10v6h-10zM10 11h12v4H10zM10 17h12v4H10zM12 23h8v6h-8z"/></svg>RETAIL<span class="arrow">›</span></div>
      <div class="cat active"><svg viewBox="0 0 32 32"><path d="M14 2h4l1 4 3 1 3-2 3 3-2 3 1 3 4 1v4l-4 1-1 3 2 3-3 3-3-2-3 1-1 4h-4l-1-4-3-1-3 2-3-3 2-3-1-3-4-1v-4l4-1 1-3-2-3 3-3 3 2 3-1zM16 11a5 5 0 100 10 5 5 0 000-10z"/></svg>INDUSTRIAL<span class="arrow">›</span></div>
      <div class="cat"><svg viewBox="0 0 32 32"><path d="M11 3h10v26H11zM15 7a3 3 0 100 6 3 3 0 000-6z"/></svg>JANITORIAL<span class="arrow">›</span></div>
    </aside>
    <div class="products">
      <div class="products-head"><h2 class="section-title">RETAIL SUPPLIES</h2><span class="view-all">VIEW ALL</span></div>
      <div class="grid">
        <div class="product"><div class="thumb"><div role="img" aria-label="Box of adhesive bandages" style="background:linear-gradient(135deg,#d9e8ef,#6fb7c9)"></div></div><p class="name">Lorem ipsum dolor sit amet</p><div class="row"><span>$. 05.00</span><span class="details">VIEW DETAILS ›</span></div></div>
        <div class="product"><div class="thumb"><div role="img" aria-label="Calculator, stapler and pen holder" style="background:linear-gradient(135deg,#555,#b0b0b0 60%,#d98a3a)"></div></div><p class="name">Lorem ipsum dolor sit amet</p><div class="row"><span>$. 12.00</span><span class="details">VIEW DETAILS ›</span></div></div>
        <div class="product"><div class="thumb"><div role="img" aria-label="Three energy-saving light bulbs" style="background:linear-gradient(135deg,#f2f2f2,#c8ccd2)"></div></div><p class="name">Lorem ipsum dolor sit amet</p><div class="row"><span>$. 24.00</span><span class="details">VIEW DETAILS ›</span></div></div>
        <div class="product"><div class="thumb"><div role="img" aria-label="Stacked red, yellow and blue storage bins" style="background:linear-gradient(135deg,#d43a2a,#f0c419 50%,#2f6fc0)"></div></div><p class="name">Lorem ipsum dolor sit amet</p><div class="row"><span>$. 0200</span><span class="details">VIEW DETAILS ›</span></div></div>
        <div class="product"><div class="thumb"><div role="img" aria-label="Roadside emergency kit with bag and warning triangle" style="background:linear-gradient(135deg,#c8241c,#e86a3a 55%,#444)"></div></div><p class="name">Lorem ipsum dolor sit amet</p><div class="row"><span>$. 14.00</span><span class="details">VIEW DETAILS ›</span></div></div>
        <div class="product"><div class="thumb"><div role="img" aria-label="Rolls of paper towel" style="background:linear-gradient(135deg,#fafafa,#d6d6d6)"></div></div><p class="name">Lorem ipsum dolor sit amet</p><div class="row"><span>$. 21.00</span><span class="details">VIEW DETAILS ›</span></div></div>
      </div>
    </div>
  </div>
</section>

<section class="features">
  <div class="wrap">
    <div class="feature"><div class="icon"><svg viewBox="0 0 28 28"><path d="M2 7h24v14H2zM4 9v10h20V9zM14 10a4 4 0 100 8 4 4 0 000-8z"/></svg></div><h4>BUDGET CONTROLS</h4><p>Ut wisi enim ad minim veniam, quis nostrud exerci tation ullamc orper suscipit.</p></div>
    <div class="feature"><div class="icon"><svg viewBox="0 0 28 28"><path d="M5 3h11l5 5v17H5zM15 4v5h5z"/></svg></div><h4>ORDER RESTRICTIONS</h4><p>Lorem ipsum dolor sit amet, conse ctetuer adipiscing elit, sed diam nonummy nibh.</p></div>
    <div class="feature"><div class="icon"><svg viewBox="0 0 28 28"><path d="M3 11h5l12-7v20l-12-7H3zM8 18h4l2 6h-4z"/></svg></div><h4>MULTI-LEVEL APPROVALS</h4><p>Sed diam nonummy nibh euismod tincidunt ut laoreet dolore magna aliquam erat volutpat.</p></div>
    <div class="feature"><div class="icon"><svg viewBox="0 0 28 28"><path d="M14 3l5 8h-4l-1-2-4 7-4-2zM24 14l3 5-5 8-2-5h3l-2-3zM4 18l3 5h9v4H6l-5-7z"/></svg></div><h4>ORDER CYCLE MANAGEMENT</h4><p>Ut wisi enim ad minim veniam, quis nostrud exerci tation ullamc orper suscipit.</p></div>
  </div>
</section>

<footer>
  <div class="site-footer">
    <div class="wrap">
      <div class="foot-col">
        <span class="foot-brand-mark"></span>
        <div class="foot-brand">MAPLEWICK HAVEN SUPPLY</div>
        <div class="foot-tag">Packaging • Printing • Distribution</div>
        <p class="foot-about">Lorem ipsum dolor sit amet, consectetuer adipiscing elit, sed diam nonummy nibh euismod tincidunt.</p>
      </div>
      <div class="foot-col contact">
        <h4>CONTACT US</h4>
        <ul>
          <li><svg viewBox="0 0 13 14"><path d="M6.5 0a4.5 4.5 0 014.5 4.5C11 8 6.5 14 6.5 14S2 8 2 4.5A4.5 4.5 0 016.5 0zm0 3a1.5 1.5 0 100 3 1.5 1.5 0 000-3z"/></svg><span>RETAIL CENTRAL<br>234, Lorem Ipsm., Lorem Ipsm,<br>Lorem Ipsm - 123 456</span></li>
          <li><svg viewBox="0 0 13 14"><path d="M0 3h13v9H0zM1 4l5.5 4L12 4z"/></svg><span>support@maplewickhaven.com</span></li>
          <li><svg viewBox="0 0 13 14"><path d="M2 1h3l1 3-2 1.5a8 8 0 004 4L9.5 8l3 1v3a1 1 0 01-1 1A11 11 0 011 2a1 1 0 011-1z"/></svg><span>123 456 789 000</span></li>
        </ul>
      </div>
      <div class="foot-col links">
        <h4>QUICK LINKS</h4>
        <ul>
          <li>About Us</li><li>Distribution</li><li>Privacy Policy</li><li>Printing</li><li>Terms of Use</li><li>Packagin</li><li>Contact Us</li><li>Products</li><li>Site Map</li>
        </ul>
      </div>
      <div class="foot-col social">
        <h4>FOLLOW ON</h4>
        <ul>
          <li><i style="background:#5a83c4"></i>Friendbook</li><li><i style="background:#4aa8e0"></i>Chirper</li><li><i style="background:#2d7ab5"></i>WorkLink</li><li><i style="background:#d3472f"></i>Circles+</li><li><i style="background:#f08a24"></i>RSS</li>
        </ul>
      </div>
    </div>
  </div>
  <div class="foot-bottom">
    <div class="wrap">
      <span>Copyright © 2015 Maplewick Haven Supply. All rights reserved.</span>
      <div class="cards"><span style="background:#d9452c"></span><span style="background:#e8e8e8"></span><span style="background:#1d4fa3"></span><span style="background:#f2f2f2"></span><span style="background:#4aa3d8"></span></div>
    </div>
  </div>
</footer>

</body>
</html>
```